Baby Boutique Needs a Business Card Design

We need a modern double sided business card design using the attached logo for Little Wren Nook.

Little Wren Nook is a baby boutique which sells only handmade clothing and accessories for both boys and girls. Our store will live exclusively online.

We would like to only use the colors that have been used in the logo.

Target Market(s)

Potential wholesale clients, Small business owners

Industry/Entity Type

Retail

Contact Information for Business Card

Name Gideon R. Falkner (Owner)
Email sales@littlewrennook.example
Main Phone 555-203-7719
Cell phone 555-203-7746
Website www.LittleWrenNook.example

Font styles to use
Sans Serif

Colors

Designer to choose colors to be used in the design.

Requirements
Must have
• -Would like to have icons that indentify the contact information.
• -Include our website
• -Include our tagline in a small area near the bottom. "Handmade Baby Creations"
• -Would like to include Facebook and Instagram Icons
• -
Nice to have
• Would like to have a simple back side with the logo.
• Something along the lines of the meadowfield lending card attached.

```html
<!DOCTYPE html>
<html lang="en">
<head>
<meta charset="utf-8">
<title>Little Wren Nook — Business Card</title>
<link href="https://fonts.googleapis.com/css2?family=Oswald:wght@500&family=Work+Sans:wght@400;500&display=swap" rel="stylesheet">
<style>
  :root {
    --stage: #3b3431;
    --card: #1d1d1f;
    --card-edge: #5fb8a9;
    --coral: #e35d5f;
    --teal: #74d3c1;
    --band-text: #2a1c1c;
    --logo-tone: #4a4a4d;
  }
  * { box-sizing: border-box; margin: 0; padding: 0; }
  html, body { width: 1200px; height: 715px; overflow: hidden; }
  body {
    background: var(--stage);
    font-family: "Work Sans", Arial, sans-serif;
    position: relative;
  }
  .card {
    position: absolute;
    top: 209px;
    width: 520px;
    height: 297px;
    background: var(--card);
    border-radius: 4px;
    overflow: hidden;
    box-shadow: 0 0 0 2px var(--card-edge);
  }
  .card--front { left: 50px; }
  .card--back { left: 630px; }

  /* Front: logo side */
  .brand {
    position: absolute;
    inset: 0;
    display: flex;
    align-items: center;
    justify-content: center;
    gap: 14px;
  }
  .brand__dot {
    width: 16px; height: 16px;
    border-radius: 50%;
    background: var(--logo-tone);
  }
  .brand__name {
    font-family: "Work Sans", Arial, sans-serif;
    font-weight: 500;
    font-size: 34px;
    color: var(--logo-tone);
    letter-spacing: 0.5px;
  }

  /* Back: contact side */
  .identity {
    position: absolute;
    right: 292px;
    top: 104px;
    text-align: right;
  }
  .identity__name {
    font-family: "Oswald", "Arial Narrow", sans-serif;
    font-weight: 500;
    font-size: 25px;
    color: var(--coral);
    text-transform: uppercase;
    letter-spacing: 0.3px;
    white-space: nowrap;
    line-height: 1.1;
  }
  .identity__role {
    font-size: 13px;
    color: var(--teal);
    margin-top: 2px;
  }
  .divider {
    position: absolute;
    left: 244px;
    top: 96px;
    width: 1.5px;
    height: 60px;
    background: var(--teal);
  }
  .contacts {
    position: absolute;
    left: 258px;
    top: 108px;
    list-style: none;
  }
  .contacts li {
    display: flex;
    align-items: center;
    gap: 7px;
    font-size: 12.5px;
    color: var(--teal);
    line-height: 17px;
    white-space: nowrap;
  }
  .contacts svg { width: 9px; height: 9px; flex: none; }
  .social {
    position: absolute;
    right: 52px;
    bottom: 56px;
    display: flex;
    gap: 10px;
  }
  .social__mark {
    width: 16px; height: 16px;
    background: var(--coral);
    border-radius: 3px;
  }
  .rule {
    position: absolute;
    left: 0; right: 0;
    bottom: 32px;
    height: 1.5px;
    background: var(--teal);
  }
  .tagline-band {
    position: absolute;
    left: 0; right: 0; bottom: 0;
    height: 28px;
    background: var(--coral);
    display: flex;
    align-items: center;
    padding-left: 150px;
  }
  .tagline {
    font-size: 12.5px;
    color: var(--band-text);
    letter-spacing: 0.6px;
  }
</style>
</head>
<body>

  <section class="card card--front" aria-label="Card front">
    <div class="brand">
      <span class="brand__dot"></span>
      <span class="brand__name">Little Wren Nook</span>
    </div>
  </section>

  <section class="card card--back" aria-label="Card back">
    <div class="identity">
      <p class="identity__name">Gideon R. Falkner</p>
      <p class="identity__role">Owner</p>
    </div>
    <div class="divider"></div>
    <ul class="contacts">
      <li>
        <svg viewBox="0 0 10 10" aria-hidden="true"><path d="M2 1 L4 1 L4.5 3 L3.3 3.8 Q4.5 6 6.2 6.7 L7 5.5 L9 6 L9 8 Q9 9 8 9 Q1 8.5 1 2 Q1 1 2 1 Z" fill="var(--coral)"/></svg>
        555-203-7719
      </li>
      <li>
        <svg viewBox="0 0 10 10" aria-hidden="true"><rect x="2.5" y="0.5" width="5" height="9" rx="1" fill="none" stroke="var(--coral)" stroke-width="1.2"/><circle cx="5" cy="7.8" r="0.6" fill="var(--coral)"/></svg>
        555-203-7746
      </li>
      <li>
        <svg viewBox="0 0 10 10" aria-hidden="true"><rect x="0.8" y="2" width="8.4" height="6" fill="none" stroke="var(--coral)" stroke-width="1.2"/><path d="M1 2.3 L5 5.5 L9 2.3" fill="none" stroke="var(--coral)" stroke-width="1.1"/></svg>
        sales@littlewrennook.example
      </li>
      <li>
        <svg viewBox="0 0 10 10" aria-hidden="true"><circle cx="5" cy="5" r="4" fill="none" stroke="var(--coral)" stroke-width="1.1"/><ellipse cx="5" cy="5" rx="1.7" ry="4" fill="none" stroke="var(--coral)" stroke-width="0.9"/><path d="M1 5 H9" stroke="var(--coral)" stroke-width="0.9"/></svg>
        www.LittleWrenNook.example
      </li>
    </ul>
    <div class="social" aria-label="Social profiles">
      <span class="social__mark"></span>
      <span class="social__mark"></span>
    </div>
    <div class="rule"></div>
    <div class="tagline-band">
      <p class="tagline">Handmade Baby Creations</p>
    </div>
  </section>

</body>
</html>
```